Create a cover for English Grammar Workbook

This book describes a system to learn English in a proper way - we call it The ''Lantern Row'' System.

It focuses on not only teaching grammar and its structures, but also giving students tips on how to use it and the best ways to remember what they learn.

The cover should have 3 realistic pillars (3D), with one closer to the front to show that this book is the 1st (front) Pillar.

The title is: "Building Sentences That Stick: *A Friendly Path Through Usage"*

Author's name: Doreen Calloway

```html
<!DOCTYPE html>
<html lang="en">
<head>
<meta charset="UTF-8">
<title>Building Sentences That Stick – Book Cover</title>
<link href="https://fonts.googleapis.com/css2?family=Bebas+Neue&family=Montserrat:wght@500;600&display=swap" rel="stylesheet">
<style>
  :root {
    --page-bg: #ffffff;
    --cover-bg: #000000;
    --band-red: #d7191f;
    --ink-light: #ffffff;
    --stone-light: #eeeeec;
    --stone-mid: #c9c9c6;
    --stone-dark: #8e8e8b;
  }
  * { margin: 0; padding: 0; box-sizing: border-box; }
  html, body {
    width: 1200px;
    height: 843px;
    overflow: hidden;
    background: var(--page-bg);
  }
  .canvas {
    position: relative;
    width: 1200px;
    height: 843px;
  }
  .book-cover {
    position: absolute;
    left: 357px;
    top: 67px;
    width: 498px;
    height: 702px;
    background: var(--cover-bg);
    overflow: hidden;
  }
  .title-lead {
    position: absolute;
    top: 36px;
    left: 0;
    width: 100%;
    text-align: center;
    font-family: "Bebas Neue", "Oswald", sans-serif;
    font-size: 56px;
    line-height: 1;
    letter-spacing: 1px;
    color: var(--ink-light);
  }
  .title-main {
    position: absolute;
    top: 92px;
    left: 0;
    width: 100%;
    text-align: center;
    font-family: "Bebas Neue", "Oswald", sans-serif;
    font-size: 124px;
    line-height: 1;
    letter-spacing: 1px;
    color: var(--ink-light);
  }
  .title-band {
    position: absolute;
    top: 206px;
    left: 0;
    width: 100%;
    height: 94px;
    background: var(--band-red);
    display: flex;
    align-items: center;
    justify-content: center;
    font-family: "Bebas Neue", "Oswald", sans-serif;
    font-size: 104px;
    line-height: 1;
    letter-spacing: 2px;
    color: var(--ink-light);
    padding-top: 8px;
  }
  .subtitle {
    position: absolute;
    top: 318px;
    left: 0;
    width: 100%;
    text-align: center;
    font-family: "Montserrat", sans-serif;
    font-weight: 600;
    font-size: 19px;
    letter-spacing: 2.6px;
    color: var(--ink-light);
    text-transform: uppercase;
  }
  .pillars {
    position: absolute;
    left: 0;
    top: 340px;
    width: 498px;
    height: 306px;
  }
  .author-band {
    position: absolute;
    left: 0;
    bottom: 0;
    width: 100%;
    height: 56px;
    background: var(--band-red);
    display: flex;
    align-items: center;
    justify-content: center;
    font-family: "Montserrat", sans-serif;
    font-weight: 600;
    font-size: 24px;
    letter-spacing: 6px;
    color: var(--ink-light);
    text-transform: uppercase;
  }
</style>
</head>
<body>
  <main class="canvas">
    <section class="book-cover">
      <h1 class="title-lead">Building</h1>
      <p class="title-main">Sentences</p>
      <p class="title-band">That Stick</p>
      <p class="subtitle">A Friendly Path Through Usage</p>

      <svg class="pillars" viewBox="0 0 498 306" role="img" aria-label="Three white classical stone columns, the centre column taller and closer to the front">
        <defs>
          <linearGradient id="stone" x1="0" y1="0" x2="1" y2="0">
            <stop offset="0" stop-color="var(--stone-dark)"/>
            <stop offset="0.45" stop-color="var(--stone-light)"/>
            <stop offset="1" stop-color="var(--stone-mid)"/>
          </linearGradient>
        </defs>
        <rect class="pillar-area pillar-left" x="76" y="76" width="100" height="230" fill="url(#stone)"/>
        <rect class="pillar-area pillar-centre" x="190" y="0" width="118" height="306" fill="url(#stone)"/>
        <rect class="pillar-area pillar-right" x="320" y="76" width="100" height="230" fill="url(#stone)"/>
      </svg>

      <p class="author-band">Doreen Calloway</p>
    </section>
  </main>
</body>
</html>
```